Business card for a Exhibition booth fabrication company

Hi. My company would like to change our corporate name card. We are an events and Exhibition stand builder company. We would like our corporate name card to resonate what we do. I need someone to create something unique that relates to the industry that I am in. The graphic designer should be creative to incorporate the elements of my industry and try to blend in well in the design of the card. Our aim is to ensure that we are unique and our card can look different from our competitors.
Updates

Target Market(s)

Marketing and events manager from all companies

Contact Information for Business Card

The business card should have the following details:
Name
Job Title
Email
Website

Colors

Designer to choose colors to be used in the design.

Requirements
Must have
• The card must be look something that is relevant to the service that I am providing. My website is: www.velmora-buildworks.com
• You can see my website to get more information on what service that I am doing
Nice to have
• On the back of my card, I would like to have a globe image with the incorporation of my company logo. This is to indicate that my services can be done in any part of the world.

```html
<!DOCTYPE html>
<html lang="en">
<head>
<meta charset="utf-8">
<title>Velmora Buildworks – Business Card</title>
<link rel="stylesheet" href="https://fonts.googleapis.com/css2?family=Open+Sans:wght@400;600;700&display=swap">
<style>
  :root {
    --brand-red: #e3151f;
    --wave-grey: #8a8a8a;
    --wave-light: #c9c9c9;
    --frame-line: #dcdcdc;
    --ink: #3a3a3a;
    --ink-soft: #555555;
    --card: #ffffff;
    --backdrop: #e6e3e1;
    --map-tone: #e4e4e4;
  }
  * { box-sizing: border-box; margin: 0; padding: 0; }
  html, body { width: 1200px; height: 997px; overflow: hidden; }
  body {
    background: var(--backdrop);
    font-family: "Open Sans", Arial, sans-serif;
    position: relative;
  }
  .card {
    position: absolute;
    left: 260px;
    width: 680px;
    height: 388px;
    background: var(--card);
    overflow: hidden;
    box-shadow: 0 6px 18px rgba(0,0,0,0.12);
  }
  .card--front { top: 90px; }
  .card--back { top: 520px; }

  /* Front: exhibition stand frame behind the brand */
  .stand-frame {
    position: absolute;
    left: 30px;
    top: 34px;
    width: 340px;
    height: 230px;
  }
  .front-brand {
    position: absolute;
    left: 70px;
    top: 112px;
    display: flex;
    align-items: center;
    gap: 12px;
  }
  .brand-dot {
    width: 22px; height: 22px;
    border-radius: 50%;
    background: var(--brand-red);
    flex: none;
  }
  .brand-name {
    color: var(--brand-red);
    font-weight: 700;
    font-size: 26px;
    letter-spacing: 2px;
    line-height: 1.1;
  }
  .front-divider {
    position: absolute;
    left: 390px;
    top: 24px;
    width: 1px;
    height: 166px;
    background: #d6d6d6;
  }
  .contact {
    position: absolute;
    left: 412px;
    top: 22px;
    color: var(--ink-soft);
    font-size: 13px;
    line-height: 1.45;
  }
  .contact__name {
    color: var(--brand-red);
    font-weight: 700;
    font-size: 15px;
    letter-spacing: 0.5px;
  }
  .contact__title { margin-bottom: 4px; }
  .contact__row { display: flex; align-items: center; gap: 8px; }
  .contact__row svg { width: 11px; height: 11px; flex: none; }
  .contact__address { margin-top: 6px; padding-left: 19px; }
  .front-wave { position: absolute; left: 0; bottom: 0; width: 680px; height: 180px; }

  /* Back */
  .world-map {
    position: absolute;
    left: 140px;
    top: 50px;
    width: 420px;
    height: 250px;
    border-radius: 50% / 45%;
    background: radial-gradient(ellipse at center, var(--map-tone) 0%, rgba(228,228,228,0.5) 55%, rgba(255,255,255,0) 75%);
  }
  .back-brand {
    position: absolute;
    left: 0; right: 0;
    top: 160px;
    display: flex;
    justify-content: center;
    align-items: center;
    gap: 14px;
  }
  .back-brand .brand-name { color: var(--ink); font-size: 30px; letter-spacing: 4px; }
  .back-web {
    position: absolute;
    left: 0; right: 0;
    top: 212px;
    text-align: center;
    color: var(--ink-soft);
    font-size: 14px;
    letter-spacing: 1px;
  }
</style>
</head>
<body>

  <section class="card card--front" aria-label="Business card front">
    <svg class="stand-frame" viewBox="0 0 340 230" aria-hidden="true">
      <g fill="none" stroke="var(--frame-line)" stroke-width="2">
        <rect x="10" y="8" width="320" height="26"/>
        <line x1="10" y1="34" x2="10" y2="200"/>
        <line x1="330" y1="34" x2="330" y2="200"/>
        <line x1="60" y1="34" x2="60" y2="200"/>
        <line x1="280" y1="34" x2="280" y2="200"/>
        <line x1="10" y1="200" x2="330" y2="200"/>
        <rect x="110" y="150" width="120" height="50"/>
        <line x1="110" y1="160" x2="230" y2="160"/>
      </g>
    </svg>
    <div class="front-brand">
      <span class="brand-dot"></span>
      <span class="brand-name">VELMORA<br>BUILDWORKS</span>
    </div>
    <div class="front-divider"></div>
    <div class="contact">
      <div class="contact__name">DANIEL HARGROVE</div>
      <div class="contact__title">President</div>
      <div class="contact__row">
        <svg viewBox="0 0 12 12"><path d="M2.5 1 4.5 3 3.5 4.5c.7 1.6 2 2.9 3.5 3.6L8.5 7l2 2-1.2 1.7C5.5 10.4 1.6 6.5 1 2.5z" fill="var(--brand-red)"/></svg>
        <span>+974 5550 1234</span>
      </div>
      <div class="contact__row">
        <svg viewBox="0 0 12 12"><circle cx="6" cy="6" r="4.5" fill="none" stroke="var(--brand-red)" stroke-width="1.6"/></svg>
        <span>+974 5550 1234</span>
      </div>
      <div class="contact__row">
        <svg viewBox="0 0 12 12"><rect x="1" y="2.5" width="10" height="7" fill="var(--brand-red)"/><path d="M1 2.5 6 6.5 11 2.5" fill="none" stroke="#fff" stroke-width="1"/></svg>
        <span>info@velmora-buildworks.com</span>
      </div>
      <div class="contact__row">
        <svg viewBox="0 0 12 12"><circle cx="6" cy="6" r="4.7" fill="none" stroke="var(--brand-red)" stroke-width="1.2"/><path d="M1.3 6h9.4M6 1.3c-2.4 2.6-2.4 6.8 0 9.4M6 1.3c2.4 2.6 2.4 6.8 0 9.4" fill="none" stroke="var(--brand-red)" stroke-width="1"/></svg>
        <span>www.velmora-buildworks.com</span>
      </div>
      <div class="contact__address">P.O. Box 4120,<br>Harbour Lane, West District</div>
    </div>
    <svg class="front-wave" viewBox="0 0 680 220" preserveAspectRatio="none" aria-hidden="true">
      <path d="M0 150 C180 150 300 110 420 70 C520 35 600 25 680 20 L680 34 C600 40 520 55 420 95 C300 140 180 165 0 168 Z" fill="var(--wave-light)"/>
      <path d="M0 168 C180 165 300 140 420 95 C520 55 600 45 680 38 L680 50 C600 58 520 70 420 110 C300 155 180 175 0 178 Z" fill="var(--wave-grey)"/>
      <path d="M0 178 C180 175 300 155 420 110 C520 70 600 60 680 52 L680 220 L0 220 Z" fill="var(--brand-red)"/>
    </svg>
  </section>

  <section class="card card--back" aria-label="Business card back">
    <div class="world-map" role="img" aria-label="Faint grey world map in the background"></div>
    <div class="back-brand">
      <span class="brand-dot"></span>
      <span class="brand-name">VELMORA BUILDWORKS</span>
    </div>
    <div class="back-web">www.velmora-buildworks.com</div>
  </section>

</body>
</html>
```